Business Card Design 2018 Kestrel Machining

Hello,

We need a business card design to reflect our new website we just had designed ( http://www.kestrelmachining.ca/)

We are a growing machine shop looking to grow our clientele and are hoping to update our current business card design to match our website and industry

The colours and design of our website should match to achieve what we are looking for.

I have attached a few images for reference as well as our logo and ISO 9000 needs to be apparent on the card as well

Please let me know what you have :)
Please copy marla@kestrelmachining.ca on all communication regarding this project

Thanks !!!

Industry/Entity Type

Business

Contact Information for Business Card

Company Name, employee name and title and contact details

Colors
f78f20
ffffff
00a990

Requirements
Must have
• Our logo, Iso 9000 same colours as our website http://www.kestrelmachining.ca/

```html
<!DOCTYPE html>
<html lang="en">
<head>
<meta charset="utf-8">
<title>Kestrel Machining — Business Card</title>
<link href="https://fonts.googleapis.com/css2?family=Roboto:wght@400;700&family=Roboto+Condensed:wght@400;500;700&display=swap" rel="stylesheet">
<style>
  :root {
    --backdrop: #e8e5e0;
    --paper: #f6f6f5;
    --teal: #1f9ea4;
    --teal-light: #3fc3cc;
    --teal-dark: #12878d;
    --ink: #1a1a1a;
    --text-grey: #4a4a4a;
    --rule: #5a5a5a;
    --white: #ffffff;
  }
  * { margin: 0; padding: 0; box-sizing: border-box; }
  html, body { width: 1200px; height: 960px; overflow: hidden; }
  body { background: var(--backdrop); position: relative; font-family: "Roboto", Arial, sans-serif; }

  .card { position: absolute; width: 600px; height: 342px; box-shadow: 0 3px 8px rgba(0,0,0,.35); overflow: hidden; }

  /* Front */
  .card-front { left: 314px; top: 113px; background: var(--paper); }
  .front-logo { position: absolute; right: 40px; top: 52px; display: flex; align-items: center; gap: 8px; }
  .logo-square { width: 22px; height: 22px; background: var(--teal); }
  .front-logo .logo-name { font-family: "Roboto Condensed", Arial, sans-serif; font-weight: 700; font-size: 27px; color: var(--ink); letter-spacing: .5px; }
  .name-tab { position: absolute; left: 0; top: 153px; width: 15px; height: 39px; background: linear-gradient(90deg, var(--teal-dark), var(--teal-light)); }
  .person-name { position: absolute; left: 40px; top: 148px; font-family: "Roboto Condensed", Arial, sans-serif; font-size: 24px; color: var(--teal); font-weight: 500; }
  .person-title { position: absolute; left: 40px; top: 177px; font-size: 14px; color: var(--ink); }
  .divider { position: absolute; left: 40px; top: 204px; width: 521px; height: 1px; background: var(--rule); }
  .contact-list { position: absolute; left: 40px; top: 218px; list-style: none; }
  .contact-list li { display: flex; align-items: center; gap: 9px; height: 19px; font-size: 14px; color: var(--text-grey); }
  .contact-list svg { width: 14px; height: 14px; fill: var(--teal); }
  .address { position: absolute; right: 39px; top: 253px; text-align: right; font-size: 14px; line-height: 19px; color: var(--text-grey); }
  .front-band { position: absolute; left: 0; bottom: 0; width: 600px; height: 37px; }
  .front-web { position: absolute; right: 38px; bottom: 11px; font-size: 14px; color: var(--white); letter-spacing: 1px; }

  /* Back */
  .card-back { left: 312px; top: 472px; background: radial-gradient(ellipse at 50% 45%, var(--teal-light) 0%, #23aab1 45%, var(--teal-dark) 100%); }
  .cert-badges { position: absolute; right: 28px; top: 24px; display: flex; gap: 14px; }
  .cert-badge { height: 24px; background: var(--white); border-radius: 2px; }
  .cert-badge.quality { width: 82px; }
  .cert-badge.partner { width: 76px; }
  .back-logo { position: absolute; left: 0; right: 0; top: 142px; display: flex; justify-content: center; align-items: center; gap: 12px; }
  .back-logo .logo-square { width: 40px; height: 40px; background: var(--white); }
  .back-logo .logo-name { font-family: "Roboto Condensed", Arial, sans-serif; font-weight: 700; font-size: 44px; color: var(--white); letter-spacing: .5px; }
  .back-web { position: absolute; left: 0; right: 0; top: 287px; text-align: center; font-size: 15px; color: var(--white); letter-spacing: 6px; }
</style>
</head>
<body>

<section class="card card-front">
  <div class="front-logo">
    <span class="logo-square"></span>
    <span class="logo-name">KESTREL MACHINING</span>
  </div>

  <span class="name-tab"></span>
  <h1 class="person-name">DANA WHITLOCK</h1>
  <p class="person-title">CEO/FOUNDER</p>
  <span class="divider"></span>

  <ul class="contact-list">
    <li><svg viewBox="0 0 24 24"><path d="M6.6 10.8a15.1 15.1 0 0 0 6.6 6.6l2.2-2.2a1 1 0 0 1 1-.25 11.4 11.4 0 0 0 3.6.57 1 1 0 0 1 1 1V20a1 1 0 0 1-1 1A17 17 0 0 1 3 4a1 1 0 0 1 1-1h3.5a1 1 0 0 1 1 1c0 1.250.2 2.450.57 3.57a1 1 0 0 1-.25 1z"/></svg>604 555 0182</li>
    <li><svg viewBox="0 0 24 24"><path d="M7 1h10a2 2 0 0 1 2 2v18a2 2 0 0 1-2 2H7a2 2 0 0 1-2-2V3a2 2 0 0 1 2-2zm0 3v14h10V4z"/></svg>604 555 0147</li>
    <li><svg viewBox="0 0 24 24"><path d="M6 2h12v6H6zM3 9h18a2 2 0 0 1 2 2v7h-4v4H5v-4H1v-7a2 2 0 0 1 2-2zm4 8v3h10v-3z"/></svg>604 555 0163</li>
    <li><svg viewBox="0 0 24 24"><path d="M2 5h20v14H2zm2 2v.5l8 5 8-5V7z"/></svg>marla@kestrelmachining.ca</li>
  </ul>

  <p class="address">1420 Forge Street<br>Surrey, BC V3S 2K8</p>

  <svg class="front-band" viewBox="0 0 600 37" preserveAspectRatio="none">
    <path d="M0 25 H600 V37 H0 Z" fill="var(--teal)"/>
    <path d="M0 14 H330 C323 14 320 24 313 24 H0 Z" fill="var(--ink)"/>
    <path d="M328 37 C343 37 340 0 360 0 H600 V37 Z" fill="var(--teal)"/>
  </svg>
  <span class="front-web">www.kestrelmachining.ca</span>
</section>

<section class="card card-back">
  <div class="cert-badges">
    <span class="cert-badge quality" role="img" aria-label="Quality certification badge"></span>
    <span class="cert-badge partner" role="img" aria-label="Partner listing badge"></span>
  </div>
  <div class="back-logo">
    <span class="logo-square"></span>
    <span class="logo-name">KESTREL MACHINING</span>
  </div>
  <p class="back-web">www.kestrelmachining.ca</p>
</section>

</body>
</html>
```